Harborline Auto LLC

Car Dealer Customer Service
Address: 2874 Cresthaven Road, Shelbyville, TN 37162
web: www.harborlineautoxq.net
email: harborlineautoxq@mailnest.example
Phone: (931) 555-0148
Phone: (629) 555-0173

```html
<!DOCTYPE html>
<html lang="en">
<head>
<meta charset="utf-8">
<title>Harborline Auto LLC – Business Card</title>
<link rel="stylesheet" href="https://fonts.googleapis.com/css2?family=Montserrat:wght@400;500;800&display=swap">
<style>
  :root {
    --page: #e9ebee;
    --front-blue: #1b7aab;
    --back-blue: #2a92cc;
    --gold: #e9b042;
    --white: #ffffff;
    --brand-blue: #1d78b0;
  }
  * { margin: 0; padding: 0; box-sizing: border-box; }
  html, body {
    width: 1200px; height: 960px; overflow: hidden;
    background: var(--page);
    font-family: "Montserrat", sans-serif;
  }
  .sheet {
    width: 1200px; height: 960px;
    display: flex; flex-direction: column; align-items: center; justify-content: center;
    gap: 56px;
  }
  .card {
    position: relative;
    width: 700px; height: 400px;
    border-radius: 24px;
    overflow: hidden;
    box-shadow: 0 6px 18px rgba(0,0,0,0.18);
  }
  .card-front {
    background: var(--front-blue);
    display: flex; flex-direction: column; align-items: center; justify-content: center; gap: 18px;
  }
  .brand-dot {
    width: 44px; height: 44px; border-radius: 50%;
    background: var(--gold);
  }
  .brand-name {
    font-weight: 800; text-transform: uppercase;
    letter-spacing: 1px; white-space: nowrap;
  }
  .card-front .brand-dot { width: 90px; height: 90px; }
  .card-front .brand-name { color: var(--white); font-size: 46px; }

  .card-back { background: var(--white); }
  .back-shapes { position: absolute; inset: 0; }
  .back-brand {
    position: absolute; right: 34px; top: 38px;
    display: flex; flex-direction: column; align-items: center; gap: 10px;
  }
  .back-brand .brand-dot { width: 40px; height: 40px; }
  .back-brand .brand-name { color: var(--brand-blue); font-size: 23px; }

  .contact {
    position: absolute; left: 48px; top: 150px;
    color: var(--white); font-weight: 500; font-size: 19px; line-height: 1.45;
  }
  .contact .role { margin-bottom: 2px; }
  .contact .address { padding-left: 18px; }
  .contact-list { list-style: none; margin-top: 4px; }
  .contact-list li { display: flex; align-items: center; gap: 10px; }
  .contact-list svg { width: 18px; height: 18px; flex: none; }
</style>
</head>
<body>
<main class="sheet">
  <section class="card card-front" aria-label="Card front">
    <span class="brand-dot"></span>
    <span class="brand-name">Harborline Auto</span>
  </section>

  <section class="card card-back" aria-label="Card back">
    <svg class="back-shapes" viewBox="0 0 700 400" preserveAspectRatio="none" aria-hidden="true">
      <path d="M0 0 H300 C282 60 322 110 422 158 C562 226 640 300 640 400 H0 Z" fill="var(--back-blue)"/>
      <path d="M308 0 C292 60 332 110 432 158 C572 226 650 300 650 400 L664 400 C668 300 612 226 474 164 C362 114 322 64 336 0 Z" fill="var(--gold)"/>
    </svg>

    <div class="back-brand">
      <span class="brand-dot"></span>
      <span class="brand-name">Harborline Auto</span>
    </div>

    <div class="contact">
      <p class="role">Car Dealer Customer Service</p>
      <p class="address">2874 Cresthaven Road,<br>Shelbyville, TN 37162</p>
      <ul class="contact-list">
        <li>
          <svg viewBox="0 0 24 24" aria-hidden="true"><path fill="var(--gold)" d="M6.6 10.8a15.1 15.1 0 0 0 6.6 6.6l2.2-2.2a1 1 0 0 1 1-.25 11.4 11.4 0 0 0 3.6.57 1 1 0 0 1 1 1V20a1 1 0 0 1-1 1A17 17 0 0 1 3 4a1 1 0 0 1 1-1h3.5a1 1 0 0 1 1 1c0 1.25.2 2.46.57 3.6a1 1 0 0 1-.25 1Z"/></svg>
          <span>(931) 555-0148</span>
        </li>
        <li>
          <svg viewBox="0 0 24 24" aria-hidden="true"><rect x="3" y="9" width="18" height="11" rx="2" fill="var(--gold)"/><path d="M2 8c3-4 17-4 20 0v2h-5V8H7v2H2Z" fill="var(--gold)"/><circle cx="12" cy="14.5" r="3" fill="var(--back-blue)"/></svg>
          <span>(629) 555-0173</span>
        </li>
        <li>
          <svg viewBox="0 0 24 24" aria-hidden="true"><rect x="2" y="5" width="20" height="14" rx="2" fill="var(--gold)"/><path d="M2.5 6 12 13l9.5-7" stroke="var(--back-blue)" stroke-width="1.6" fill="none"/></svg>
          <span>harborlineautoxq@mailnest.example</span>
        </li>
        <li>
          <svg viewBox="0 0 24 24" aria-hidden="true"><circle cx="12" cy="12" r="10" fill="var(--gold)"/><path d="M2 12h20M12 2c3 3 3 17 0 20M12 2c-3 3-3 17 0 20" stroke="var(--back-blue)" stroke-width="1.4" fill="none"/></svg>
          <span>www.harborlineautoxq.net</span>
        </li>
      </ul>
    </div>
  </section>
</main>
</body>
</html>
```